RW Holloway LLC Business Card - Civil Engineering & Consulting Firm

We need a Business Card that is elegant, and masculine.  It is our Professional Civil Engineering & Consulting Company located in San Antonio TX (Not s construction or builder firm- no gears & no tool images please). We provide civil engineering services including  commercial site plans, grading and drainage plans, utility plans, hydraulics and hydrology, land planning, utility coordination, and other general civil engineering services related to commercial and residential development.
We have 2 existing Logos. We would like to convey reliability, strength, trustworthiness and attention to detail.  Blues and orange tones as per logo We are OK with the use of a darker blue in the mix.  We have 2 logo versions - Full Company Name Logo to go on the back of card, & Small Icon Logo for the front w/ personal Info.

Target Market(s)
Architects, Real Estate Developers, Other Strctural Engineers, Surveyers, General Contractors
Industry/Entity Type
Professional Civil Engineering
Contact Information for Business Card
Name, Position, Address, Cell & Office #, email, and company website
Font styles to use
Other font styles liked:
- Avian
Requirements
Should not have
- No Tools, No Gears, no Cranes, or Construction Equipment.

```html
<!DOCTYPE html>
<html lang="en">
<head>
<meta charset="UTF-8">
<title>RW Holloway LLC – Business Card</title>
<link href="https://fonts.googleapis.com/css2?family=Montserrat:wght@400;500;700&display=swap" rel="stylesheet">
<style>
  :root {
    --backdrop: #1f1f21;
    --sky-blue: #78a9d2;
    --dusk-grey: #a8a3a0;
    --warm-orange: #e3933f;
    --accent-orange: #f0922b;
    --paper: #efeff0;
    --paper-shade: #dcdcde;
    --ink: #1c1c1c;
    --white: #ffffff;
  }
  * { margin: 0; padding: 0; box-sizing: border-box; }
  html, body { width: 1200px; height: 900px; overflow: hidden; }
  body {
    background: var(--backdrop);
    font-family: "Montserrat", sans-serif;
    display: flex;
    flex-direction: column;
    align-items: center;
    justify-content: center;
    gap: 32px;
  }
  .card {
    width: 640px;
    height: 366px;
    position: relative;
    overflow: hidden;
    box-shadow: 0 10px 28px rgba(0,0,0,0.55);
  }
  /* Back of card */
  .card--back {
    background: linear-gradient(180deg, var(--sky-blue) 0%, var(--dusk-grey) 50%, var(--warm-orange) 100%);
    display: flex;
    align-items: center;
    justify-content: center;
  }
  .brand-name--large {
    color: var(--white);
    font-weight: 500;
    font-size: 46px;
    letter-spacing: 4px;
    text-transform: uppercase;
  }
  /* Front of card */
  .card--front {
    background: linear-gradient(135deg, var(--paper-shade) 0%, var(--paper) 45%, #f6f6f7 70%, var(--paper-shade) 100%);
  }
  .person {
    position: absolute;
    top: 36px;
    left: 0;
    padding-left: 34px;
  }
  .person::before {
    content: "";
    position: absolute;
    left: 0;
    top: 0;
    width: 14px;
    height: 38px;
    background: var(--accent-orange);
  }
  .person__name {
    color: var(--accent-orange);
    font-weight: 700;
    font-size: 22px;
    letter-spacing: 1px;
    text-transform: uppercase;
    line-height: 1.1;
  }
  .person__role {
    color: var(--ink);
    font-size: 15px;
    margin-top: 4px;
  }
  .brand-name--small {
    position: absolute;
    right: 34px;
    top: 120px;
    color: var(--accent-orange);
    font-weight: 700;
    font-size: 16px;
    letter-spacing: 1px;
    text-align: right;
    line-height: 1.3;
  }
  .contact {
    position: absolute;
    left: 0;
    right: 0;
    bottom: 28px;
    text-align: center;
    color: var(--ink);
    font-size: 15px;
  }
  .contact__address { margin-bottom: 10px; padding-left: 90px; }
  .contact__row {
    display: flex;
    justify-content: center;
    align-items: center;
    gap: 16px;
    margin-bottom: 8px;
  }
  .contact__item { display: inline-flex; align-items: center; gap: 7px; }
  .icon { width: 16px; height: 16px; fill: var(--accent-orange); flex-shrink: 0; }
</style>
</head>
<body>
  <section class="card card--back">
    <span class="brand-name--large">RW Holloway LLC</span>
  </section>

  <section class="card card--front">
    <div class="person">
      <p class="person__name">Dane Whitcombe</p>
      <p class="person__role">Co-Founder</p>
    </div>

    <p class="brand-name--small">RW Holloway<br>LLC</p>

    <div class="contact">
      <p class="contact__address">4180 N. Ridge Road Suite 210 Alamo 14</p>
      <div class="contact__row">
        <span class="contact__item">
          <svg class="icon" viewBox="0 0 24 24" aria-hidden="true"><path d="M6.6 10.8a15 15 0 0 0 6.6 6.6l2.2-2.2c.3-.3.7-.4 1-.2 1.1.4 2.3.6 3.6.6.6 0 1 .4 1 1V20c0 .6-.4 1-1 1A17 17 0 0 1 3 4c0-.6.4-1 1-1h3.5c.6 0 1 .4 1 1 0 1.3.2 2.5.6 3.6.1.3 0 .7-.2 1z"/></svg>
          555-214-0381
        </span>
        <span class="contact__item">
          <svg class="icon" viewBox="0 0 24 24" aria-hidden="true"><path d="M3 9c0-3 4-4 9-4s9 1 9 4v1h-4V8.5c-1.5-.5-3-.7-5-.7s-3.5.2-5 .7V10H3z"/><rect x="5" y="11" width="14" height="9" rx="1.5"/></svg>
          555-214-0472
        </span>
        <span class="contact__item">
          <svg class="icon" viewBox="0 0 24 24" aria-hidden="true"><path d="M2 5h20v14H2z M2 5l10 8 10-8" fill="var(--accent-orange)"/><path d="M2 5l10 8 10-8" fill="none" stroke="#fff" stroke-width="1.5"/></svg>
          info@rwhollowayllc
        </span>
      </div>
      <div class="contact__row">
        <span class="contact__item">
          <svg class="icon" viewBox="0 0 24 24" aria-hidden="true"><circle cx="12" cy="12" r="10"/><path d="M2 12h20M12 2c3 3 3 17 0 20M12 2c-3 3-3 17 0 20" fill="none" stroke="#fff" stroke-width="1.3"/></svg>
          www.hollowaycivil.com
        </span>
      </div>
    </div>
  </section>
</body>
</html>
```